Restyle corporate identity (+ logo) for a road construction company

We need a new logo and stationary design for our company VARNOK path. VARNOK path® increases the road base strength, while reducing major costs and time of road construction. Attached some examples of the current design.

Our wishes for the new logo:
- Business look
- Style sheet
- Modern

More information: www.varnokpath.example
Updates

Target Market(s)

Government

Industry/Entity Type

Construction

Requirements
Must have
• Logo (with road sign) + text

```html
<!DOCTYPE html>
<html lang="en">
<head>
<meta charset="utf-8">
<title>VARNOK path stationery</title>
<link href="https://fonts.googleapis.com/css2?family=Arimo:wght@400;700&display=swap" rel="stylesheet">
<style>
:root{
  --green:#9bc31f;
  --grey:#8c8c8c;
  --dark:#5f5f5f;
  --orange:#f08a24;
  --paper:#ffffff;
  --bg:#efefef;
  --ink:#444444;
}
*{margin:0;padding:0;box-sizing:border-box}
html,body{width:1200px;height:937px;overflow:hidden;background:var(--bg);font-family:"Arimo",Arial,sans-serif;color:var(--ink)}
.canvas{position:relative;width:1200px;height:937px}
.sheet{position:absolute;background:var(--paper);overflow:hidden;box-shadow:0 2px 8px rgba(0,0,0,.12)}
.brand{display:flex;align-items:center;gap:8px;color:var(--grey);font-weight:700;white-space:nowrap}
.brand-dot{border-radius:50%;background:var(--green);flex:none}

/* letterhead */
.letterhead{left:185px;top:66px;width:388px;height:546px}
.letterhead .brand{position:absolute;left:18px;top:26px;font-size:26px}
.letterhead .brand-dot{width:56px;height:56px}
.contacts{position:absolute;left:268px;top:26px;font-size:6.5px;line-height:11.5px;color:var(--ink);list-style:none;white-space:nowrap}
.contacts li{display:flex;align-items:center;gap:4px}
.contacts li::before{content:"";width:7px;height:7px;border-radius:50%;background:var(--orange)}
.letter{position:absolute;left:36px;top:138px;width:300px;font-size:5.6px;line-height:8px}
.letter p{margin-bottom:8px}
.letter .gap{margin-bottom:20px}
.faint-mark{position:absolute;left:108px;top:250px;width:170px;height:170px;border-radius:50%;background:var(--green);opacity:.06}
.signature{width:28px;height:16px;background:#d9d9d9;margin:4px 0 6px}
.footer-band{position:absolute;left:0;bottom:0;width:100%;height:46px}

/* cover sheet */
.cover{left:636px;top:40px;width:458px;height:576px}
.cover .brand-dot{position:absolute;left:175px;top:203px;width:108px;height:108px}
.cover .name{position:absolute;left:0;width:100%;top:316px;text-align:center;font-size:48px;font-weight:700;color:var(--grey);white-space:nowrap}

/* business cards */
.card{width:177px;height:100px;border-radius:8px}
.card-front{left:45px;top:658px}
.card-front .brand{position:absolute;left:6px;top:10px;font-size:15px;gap:5px}
.card-front .brand-dot{width:24px;height:24px}
.card-strip{position:absolute;left:0;top:40px;width:100%;height:10px}
.card-details{position:absolute;left:15px;top:53px;font-size:4.5px;line-height:6.5px}
.card-contacts{position:absolute;left:88px;top:61px;font-size:4.5px;line-height:6.5px;list-style:none;white-space:nowrap}
.card-contacts li{display:flex;align-items:center;gap:2px}
.card-contacts li::before{content:"";width:4px;height:4px;border-radius:50%;background:var(--orange)}
.card-web{position:absolute;left:15px;top:83px;font-size:4.5px;color:var(--orange)}
.card-base{position:absolute;left:0;bottom:0;width:100%;height:6px;background:var(--dark)}
.card-back{left:45px;top:785px}
.card-back .brand{position:absolute;left:28px;top:37px;font-size:15px;gap:5px}
.card-back .brand-dot{width:28px;height:28px}

/* envelopes */
.envelope-front{left:265px;top:671px;width:432px;height:209px}
.envelope-front .brand{position:absolute;left:14px;top:18px;font-size:28px}
.envelope-front .brand-dot{width:52px;height:52px}
.envelope-back{left:737px;top:671px;width:400px;height:209px}
.flap{position:absolute;left:0;top:0;width:100%;height:72px;background:var(--green);border-radius:0 0 34px 34px;color:#fff;text-align:center;font-size:15px;letter-spacing:2px;padding-top:25px}
.flap b{font-weight:700}
</style>
</head>
<body>
<div class="canvas">

  <section class="sheet letterhead">
    <div class="brand"><span class="brand-dot"></span>VARNOK path</div>
    <ul class="contacts">
      <li>012 345 6789</li>
      <li>012 345 6789</li>
      <li>012 345 6789</li>
      <li>office@varnokpath.example</li>
    </ul>
    <div class="faint-mark"></div>
    <div class="letter">
      <p>July 2, 2012</p>
      <p><b>Dear CH,</b><br>ABC Building, def St., Country Name</p>
      <p>is simply dummy text of the printing and typesetting industry. Lorem Ipsum has been the industry's standard dummy text ever since the 1500s, when an unknown printer took a galley of type and scrambled it to make a type specimen book. It has survived not only five centuries, but also the leap into electronic typesetting, remaining essentially unchanged. It was popularised in the 1960s with the release of Letraset sheets containing Lorem Ipsum passages, and more recently with desktop publishing software like Aldus PageMaker including versions of Lorem Ipsum.</p>
      <p class="gap">is simply dummy text of the printing and typesetting industry. Lorem Ipsum has been the industry's standard dummy text ever since the 1500s, when an unknown printer took a galley of type and scrambled it to make</p>
      <p>is simply dummy text of the printing and typesetting industry. Lorem Ipsum has been the industry's standard dummy text ever since the 1500s, when an unknown printer took a galley of type and scrambled it to make a type specimen book. It has survived not only five centuries, but also the leap into electronic typesetting, remaining essentially unchanged. It was popularised in the 1960s with the release of Letraset sheets containing Lorem Ipsum passages, and more recently with desktop publishing software like Aldus PageMaker including versions of Lorem Ipsum.</p>
      <p>Best Regards,</p>
      <div class="signature" role="img" aria-label="Handwritten signature"></div>
      <p><b>Daren Holt</b><br>Director<br><br>ABC Building, def St., Country Name</p>
    </div>
    <svg class="footer-band" viewBox="0 0 388 46" aria-hidden="true">
      <polygon points="0,14 106,14 110,20 4,26 0,26" fill="var(--green)"/>
      <polygon points="110,14 195,14 200,23 110,23" fill="var(--green)" opacity=".55"/>
      <rect x="110" y="22" width="278" height="1.5" fill="var(--green)"/>
      <text x="12" y="22" font-size="5" font-family="Arimo, sans-serif" fill="#fff">12 Quarry Lane, Block B</text>
      <text x="124" y="21" font-size="5" font-family="Arimo, sans-serif" fill="#444">www.varnokpath.example</text>
      <rect x="0" y="35" width="388" height="11" fill="var(--dark)"/>
    </svg>
  </section>

  <section class="sheet cover">
    <span class="brand-dot"></span>
    <div class="name">VARNOK path</div>
    <svg class="footer-band" viewBox="0 0 458 46" aria-hidden="true">
      <polygon points="14,8 192,8 200,22 14,22" fill="var(--green)"/>
      <rect x="196" y="20" width="262" height="2" fill="var(--green)"/>
      <text x="30" y="19" font-size="8" letter-spacing="1.5" font-family="Arimo, sans-serif" fill="#fff">www.varnokpath.example</text>
      <rect x="0" y="34" width="458" height="12" fill="var(--dark)"/>
    </svg>
  </section>

  <section class="sheet card card-front">
    <div class="brand"><span class="brand-dot"></span>VARNOK path</div>
    <svg class="card-strip" viewBox="0 0 177 10" aria-hidden="true">
      <polygon points="10,0 76,0 80,10 10,10" fill="var(--green)"/>
      <polygon points="80,0 124,0 128,10 84,10" fill="var(--green)" opacity=".6"/>
      <rect x="124" y="4" width="53" height="1" fill="var(--green)"/>
      <text x="14" y="7.5" font-size="6" font-weight="700" font-family="Arimo, sans-serif" fill="#fff">MARCUS ELWIN</text>
      <text x="86" y="7" font-size="4" font-family="Arimo, sans-serif" fill="#fff">Managing Director</text>
    </svg>
    <div class="card-details">12 Quarry Lane, Block B<br>North Yard</div>
    <ul class="card-contacts">
      <li>012 345 6789</li>
      <li>012 345 6789</li>
      <li>012 345 6789</li>
      <li>office@varnokpath.example</li>
    </ul>
    <div class="card-web">www.varnokpath.example</div>
    <div class="card-base"></div>
  </section>

  <section class="sheet card card-back">
    <div class="brand"><span class="brand-dot"></span>VARNOK path</div>
  </section>

  <section class="sheet envelope-front">
    <div class="brand"><span class="brand-dot"></span>VARNOK path</div>
  </section>

  <section class="sheet envelope-back">
    <div class="flap">www.<b>varnokpath</b>.example</div>
  </section>

</div>
</body>
</html>
```